Business card for Luxury Portable Restroom Trailer company

We are a Luxury Portable Restroom Trailer Company Called FALCRIDGE HIRES. Based in Orange County California. We provide portable restroom trailers for events, such as, Weddings, Concerts, Charity events, Sporting events, Tournaments, Corporate events, ect. We rent and Sell the Luxury restrooms. Our colors are white, grey, and Orange. As you will see in the logo we uploaded.
There are 2 people in the company so the names and titles will change for the 3 people but card will remain the same. Here is the information for each Person: Dwight Penner CFO 555 318-0476
next Person: Leon Marchetti VP 555 318-0476
Next Person: Owen Marchetti CEO 555 318-0476
Information to include on the card: Luxury Restroom Trailers Rental and Sales. Weddings, Concerts, Charity, Sporting and Corp. Events.

```html
<!DOCTYPE html>
<html lang="en">
<head>
<meta charset="utf-8">
<title>Falcridge Hires – Business Card</title>
<link rel="stylesheet" href="https://fonts.googleapis.com/css2?family=Montserrat:wght@400;500;800&display=swap">
<style>
  :root {
    --bg: #d9d9d9;
    --card-front: #ffffff;
    --card-back: #eeeeee;
    --grey: #5f5f5f;
    --grey-text: #4a4a4a;
    --orange: #ee6a2c;
    --orange-soft: #f29a6c;
  }
  * { margin: 0; padding: 0; box-sizing: border-box; }
  html, body { width: 1200px; height: 1200px; overflow: hidden; }
  body {
    background: var(--bg);
    font-family: "Montserrat", sans-serif;
    position: relative;
  }
  .card {
    position: absolute;
    left: 250px;
    width: 700px;
    height: 400px;
    border-radius: 22px;
    box-shadow: 0 10px 28px rgba(0,0,0,0.18);
  }
  .card--front { top: 150px; background: var(--card-front); }
  .card--back  { top: 630px; background: var(--card-back); }

  /* Brand lockup */
  .brand {
    position: absolute;
    display: flex;
    align-items: center;
    gap: 14px;
    border: 5px solid currentColor;
    padding: 22px 30px;
  }
  .brand__mark { width: 22px; height: 22px; background: currentColor; flex: none; }
  .brand__name { font-weight: 800; letter-spacing: 1px; line-height: 1; white-space: nowrap; }

  .card--front .brand { left: 95px; top: 70px; color: var(--grey); }
  .card--front .brand__name { font-size: 44px; }

  .services {
    position: absolute;
    top: 265px;
    list-style: none;
    font-size: 17px;
    font-weight: 500;
    color: var(--grey-text);
    line-height: 1.75;
  }
  .services li::before {
    content: "";
    display: inline-block;
    width: 7px; height: 7px;
    border-radius: 50%;
    background: var(--orange-soft);
    margin-right: 14px;
    vertical-align: middle;
  }
  .services--left { left: 95px; }
  .services--right { left: 380px; top: 230px; }

  .card--back .brand { left: 55px; top: 160px; color: var(--orange); padding: 16px 20px; border-width: 4px; gap: 10px; }
  .card--back .brand__mark { width: 14px; height: 14px; }
  .card--back .brand__name { font-size: 24px; }

  .divider {
    position: absolute;
    left: 395px; top: 70px;
    width: 2px; height: 260px;
    background: var(--grey-text);
  }
  .contact { position: absolute; left: 420px; top: 78px; color: var(--grey-text); }
  .contact__name { font-size: 27px; font-weight: 800; color: var(--orange); }
  .contact__title { font-size: 17px; font-weight: 500; margin: 4px 0 14px 4px; }
  .contact__address { font-size: 15px; font-weight: 500; line-height: 1.5; margin: 0 0 12px 4px; }
  .contact__lines { list-style: none; font-size: 15px; font-weight: 500; line-height: 1.9; margin-left: 4px; }
  .contact__lines li { display: flex; align-items: center; gap: 10px; }
  .contact__lines svg { width: 15px; height: 15px; fill: var(--orange); flex: none; }
</style>
</head>
<body>

<section class="card card--front">
  <div class="brand">
    <span class="brand__mark"></span>
    <span class="brand__name">FALCRIDGE HIRES</span>
  </div>
  <ul class="services services--left">
    <li>Luxury Restroom</li>
    <li>Trailers Rental and Sales</li>
    <li>Weddings</li>
  </ul>
  <ul class="services services--right">
    <li>Concerts</li>
    <li>Charity</li>
    <li>Sporting and Corp. Events</li>
  </ul>
</section>

<section class="card card--back">
  <div class="brand">
    <span class="brand__mark"></span>
    <span class="brand__name">FALCRIDGE HIRES</span>
  </div>
  <div class="divider"></div>
  <div class="contact">
    <h1 class="contact__name">Dwight Penner</h1>
    <p class="contact__title">CFO</p>
    <p class="contact__address">4178 Verlan Road<br>Dunmore Bay Oregon 97310</p>
    <ul class="contact__lines">
      <li>
        <svg viewBox="0 0 24 24"><path d="M6.6 10.8a15 15 0 0 0 6.6 6.6l2.2-2.2a1 1 0 0 1 1-.25 11.4 11.4 0 0 0 3.6.57 1 1 0 0 1 1 1V20a1 1 0 0 1-1 1A17 17 0 0 1 3 4a1 1 0 0 1 1-1h3.5a1 1 0 0 1 1 1c0 1.25.2 2.45.57 3.6a1 1 0 0 1-.25 1z"/></svg>
        555 318-0476
      </li>
      <li>
        <svg viewBox="0 0 24 24"><path d="M2 5h20v14H2z M2 5l10 8 10-8" fill="none" stroke="#ee6a2c" stroke-width="2"/><path d="M2 5h20l-10 8z"/></svg>
        info@falcridgehires.com
      </li>
      <li>
        <svg viewBox="0 0 24 24"><circle cx="12" cy="12" r="9" fill="none" stroke="#ee6a2c" stroke-width="2"/><path d="M3 12h18M12 3c3 3 3 15 0 18M12 3c-3 3-3 15 0 18" fill="none" stroke="#ee6a2c" stroke-width="2"/></svg>
        www.falcridgehires.com
      </li>
    </ul>
  </div>
</section>

</body>
</html>
```